Lumavento business card

We need a modern business card - With our 4 colors - See web: www.lumavento.dk

I have attached logo and som old business Cards we have - Lets Make the new ones shine...:-) -

Industry/Entity Type

Business

Requirements
Must have
• the logo with lumavento only,

```html
<!DOCTYPE html>
<html lang="da">
<head>
<meta charset="utf-8">
<title>Lumavento business card</title>
<link rel="stylesheet" href="https://fonts.googleapis.com/css2?family=Source+Sans+3:wght@400;600&display=swap">
<style>
  :root {
    --bg: #454545;
    --white: #ffffff;
    --green: #8cc63f;
    --purple: #6a2a76;
    --magenta: #c8338a;
    --orange: #e28a3c;
    --ink: #231f20;
    --text: #555555;
  }
  * { box-sizing: border-box; margin: 0; padding: 0; }
  html, body {
    width: 1105px; height: 1200px; overflow: hidden;
    background: var(--bg);
    font-family: "Source Sans 3", Arial, sans-serif;
  }
  .card {
    position: absolute; left: 192px;
    width: 720px; height: 412px;
    border-radius: 19px; overflow: hidden;
    background: var(--white);
  }
  .card--front { top: 146px; }
  .card--back { top: 602px; display: flex; }

  .front-band { position: absolute; inset: 0; }

  .person { position: absolute; right: 34px; top: 34px; text-align: right; color: var(--white); }
  .person__name { font-size: 27px; font-weight: 600; line-height: 1.1; }
  .person__title { font-size: 18px; line-height: 1.3; }

  .brand { position: absolute; left: 36px; top: 186px; width: 242px; text-align: center; }
  .brand__name { font-size: 25px; color: var(--ink); letter-spacing: 1px; }
  .brand__rule { height: 2px; background: var(--green); margin: 10px 0 12px; }
  .brand__tagline { font-size: 15px; color: var(--ink); }

  .contact { position: absolute; left: 36px; top: 300px; list-style: none; }
  .contact li { display: flex; align-items: center; gap: 12px; font-size: 19px; color: var(--text); height: 28px; }
  .contact svg { width: 18px; height: 18px; fill: var(--green); }

  .address { position: absolute; right: 34px; top: 300px; text-align: right; font-size: 19px; color: var(--text); line-height: 28px; }

  .stripe { height: 100%; }
  .stripe--green { width: 175px; background: var(--green); }
  .stripe--purple { width: 177px; background: var(--purple); }
  .stripe--magenta { width: 182px; background: var(--magenta); }
  .stripe--orange { flex: 1; background: var(--orange); }
  .back-name {
    position: absolute; left: 0; right: 0; top: 180px;
    text-align: center; font-size: 44px; color: var(--white); letter-spacing: 2px;
  }
</style>
</head>
<body>
  <section class="card card--front">
    <svg class="front-band" viewBox="0 0 720 412" preserveAspectRatio="none">
      <path d="M0 0 H720 V196 C560 80 280 40 0 74 Z" fill="var(--ink)"/>
      <path d="M0 0 H720 V184 C560 70 280 34 0 68 Z" fill="var(--green)"/>
    </svg>
    <div class="person">
      <div class="person__name">Jonas Maltbek</div>
      <div class="person__title">Salgsdirektør</div>
    </div>
    <div class="brand">
      <div class="brand__name">lumavento</div>
      <div class="brand__rule"></div>
      <div class="brand__tagline">medier til unge</div>
    </div>
    <ul class="contact">
      <li><svg viewBox="0 0 24 24"><path d="M6.6 10.8a15 15 0 0 0 6.6 6.6l2.2-2.2c.3-.3.7-.4 1-.2 1.1.4 2.3.6 3.6.6.6 0 1 .4 1 1V20c0 .6-.4 1-1 1A17 17 0 0 1 3 4c0-.6.4-1 1-1h3.5c.6 0 1 .4 1 1 0 1.3.2 2.5.6 3.6.1.3 0 .7-.2 1z"/></svg>+45 31 42 67 08</li>
      <li><svg viewBox="0 0 24 24"><path d="M6.6 10.8a15 15 0 0 0 6.6 6.6l2.2-2.2c.3-.3.7-.4 1-.2 1.1.4 2.3.6 3.6.6.6 0 1 .4 1 1V20c0 .6-.4 1-1 1A17 17 0 0 1 3 4c0-.6.4-1 1-1h3.5c.6 0 1 .4 1 1 0 1.3.2 2.5.6 3.6.1.3 0 .7-.2 1z"/></svg>+45 52 19 73 46</li>
      <li><svg viewBox="0 0 24 24"><path d="M2 5h20v14H2z M2 5l10 8 10-8" fill="var(--green)"/><path d="M3 6l9 7 9-7" fill="none" stroke="#fff" stroke-width="1.6"/></svg>jm@lumavento.dk</li>
    </ul>
    <div class="address">
      Solbakkevej 14<br>
      2100 Nørrelund<br>
      www.lumavento.dk
    </div>
  </section>

  <section class="card card--back">
    <div class="stripe stripe--green"></div>
    <div class="stripe stripe--purple"></div>
    <div class="stripe stripe--magenta"></div>
    <div class="stripe stripe--orange"></div>
    <div class="back-name">lumavento</div>
  </section>
</body>
</html>
```